Lanternfield Drinks business cards

We need a business card design for our new logo. The company is modern, progressive, professional, yet approachable. The key products are ready to drink bottles and cans of coffee based beverages.
These cards will be a critical part of the first impression made by our sales organization, business development team, and all external facing personnel.
Card can be a vertical or horizontal orientation.

Target Market(s)

Customers, suppliers, business partners

Industry/Entity Type

Business

Contact Information for Business Card

Business cards should feature Company Name and Logo.

Font styles to use
Serif

Colors

Designer to choose colors to be used in the design.

Requirements
Must have
• Strong readability of Name, phone #, mobile number and email address.
• Job title, website url, Street Address, and other details can be secondary level readability.
Nice to have
• High impact, simplistic quality design.
• Ok to utilize the 'H in the box' separate from the company name

```html
<!DOCTYPE html>
<html lang="en">
<head>
<meta charset="utf-8">
<title>Lanternfield Drinks – Business Cards</title>
<link rel="stylesheet" href="https://fonts.googleapis.com/css2?family=Crimson+Text:wght@400;700&display=swap">
<style>
  :root {
    --backdrop: #3b3b3c;
    --card: #1d1d1f;
    --accent: #e2552c;
    --accent-gold: #e0932a;
    --ink-light: #f2f2f2;
    --emboss: #4a4a4d;
  }
  html, body {
    margin: 0;
    padding: 0;
    width: 799px;
    height: 1200px;
    overflow: hidden;
    background: var(--backdrop);
  }
  .canvas {
    position: relative;
    width: 799px;
    height: 1200px;
    font-family: "Crimson Text", Georgia, serif;
  }
  .card {
    position: absolute;
    left: 70px;
    width: 660px;
    height: 378px;
    background: var(--card);
    border-radius: 4px;
    box-shadow: 0 10px 24px rgba(0,0,0,0.45);
    overflow: hidden;
  }
  .card--front { top: 100px; }
  .card--back { top: 700px; }

  /* Front */
  .front-mark {
    position: absolute;
    inset: 0;
    display: flex;
    align-items: center;
    justify-content: center;
    gap: 18px;
  }
  .front-mark__square {
    width: 46px;
    height: 46px;
    border: 4px solid var(--emboss);
    box-sizing: border-box;
  }
  .front-mark__name {
    color: var(--emboss);
    font-size: 40px;
    font-weight: 700;
    letter-spacing: 1px;
  }

  /* Back */
  .holder {
    position: absolute;
    left: 40px;
    top: 36px;
  }
  .holder__name {
    color: var(--accent);
    font-size: 25px;
    font-weight: 700;
    line-height: 1;
    margin: 0;
  }
  .holder__title {
    color: var(--ink-light);
    font-size: 14px;
    margin: 4px 0 0;
  }
  .contact {
    position: absolute;
    left: 40px;
    bottom: 52px;
    margin: 0;
    padding: 0;
    list-style: none;
    color: var(--ink-light);
    font-size: 17px;
    line-height: 24px;
  }
  .contact__row {
    display: flex;
    align-items: center;
    gap: 14px;
  }
  .contact__icon {
    width: 14px;
    height: 14px;
    flex: none;
  }
  .contact__address {
    margin-left: -2px;
    font-size: 17px;
  }
  .brand {
    position: absolute;
    right: 44px;
    top: 150px;
    display: flex;
    align-items: center;
    gap: 12px;
    padding-bottom: 8px;
    border-bottom: 2px solid var(--accent-gold);
  }
  .brand__square {
    width: 30px;
    height: 30px;
    border: 4px solid var(--accent);
    box-sizing: border-box;
  }
  .brand__name {
    color: var(--accent);
    font-size: 34px;
    font-weight: 700;
    letter-spacing: 1px;
    line-height: 1;
  }
</style>
</head>
<body>
<main class="canvas">

  <section class="card card--front" aria-label="Card front">
    <div class="front-mark">
      <div class="front-mark__square"></div>
      <span class="front-mark__name">Lanternfield Drinks</span>
    </div>
  </section>

  <section class="card card--back" aria-label="Card back">
    <div class="holder">
      <h1 class="holder__name">Mara Ellison Pike</h1>
      <p class="holder__title">Managing Director</p>
    </div>

    <ul class="contact">
      <li class="contact__row">
        <svg class="contact__icon" viewBox="0 0 16 16" aria-hidden="true"><path fill="var(--accent)" d="M3 1h3l1.5 4-2 1.3a9 9 0 0 0 4.2 4.2L11 8.5l4 1.5v3c0 1-1 2-2 2C6.5 15 1 9.5 1 3c0-1 1-2 2-2z"/></svg>
        <span>555.210.4821</span>
      </li>
      <li class="contact__row">
        <svg class="contact__icon" viewBox="0 0 16 16" aria-hidden="true"><rect x="4" y="1" width="8" height="14" rx="1.5" fill="var(--accent)"/><rect x="5.5" y="3" width="5" height="8" fill="var(--card)"/></svg>
        <span>555.318.6604</span>
      </li>
      <li class="contact__row">
        <svg class="contact__icon" viewBox="0 0 16 16" aria-hidden="true"><rect x="1" y="3" width="14" height="10" fill="var(--accent)"/><path d="M1 3l7 6 7-6" fill="none" stroke="var(--card)" stroke-width="1.4"/></svg>
        <span>mara@lanternfield.co</span>
      </li>
      <li class="contact__row">
        <svg class="contact__icon" viewBox="0 0 16 16" aria-hidden="true"><g fill="none" stroke="var(--accent)" stroke-width="1.5"><circle cx="8" cy="8" r="6.5"/><ellipse cx="8" cy="8" rx="3" ry="6.5"/><path d="M1.5 8h13"/></g></svg>
        <span>www.lanternfield.co</span>
      </li>
      <li class="contact__row contact__address">88 Millrace Ave., Harbor Falls, US 40512</li>
    </ul>

    <div class="brand">
      <div class="brand__square"></div>
      <span class="brand__name">Lanternfield Drinks</span>
    </div>
  </section>

</main>
</body>
</html>
```